Create a banner for me that embodies my health and well being package.

I am an intuitive counselor with a busy practice helping clients to shift their blocks and move forward in their lives.
I have created a package called '9 paths home again'
I am wanting a banner to put on my website page, facebook page and to use as a letter head in mailouts.
My ideal clients are those who want to create change in their lives and who invest money in themselves and their personal and spiritual growth.
I am different to regular life coaches as my sessions have a spiritual twist to them creating much deeper change in my clients.
I would like the banner to be mainly font with the title of the progam: 9 Paths Home Again (no other wording) (something along the lines of the Blackjack font) and that ties in with the theme of my website. I'm not sure what else I want with it and am looking for ideas.
Website:
www.lumorawellspring.com.au
I also have a current facebook page for the business:
https://www.facebook.com/Lumora-Wellspring-Studio-502718364091557/
(Note: I am about to drop my logo and business name and move to using my own name - the rest of the website will remain the same).
I have attached a doc with the draft of what wording will be on the website page any advertising will link to, to give you an idea of what the program is about.

Target Market(s)

People who invest money on themselves who are looking to improve their emotional well being and creating change in their life. Majority are middle aged women (also younger females and some men)

Industry/Entity Type

Health And Wellness

Font styles to use
Other font styles liked:
• I like Blackjack and Amienne. Along those lines.

Requirements
Must have
• Attractive, modern and GREAT font.
Nice to have
• Surprise me with something amazing!
• I love the colours in the 2 images I have up loaded as they represent the heart chakra colours. They could be a feature on the banner or blurred into the background.
Should not have
• Even though my work is quite spiritual I don't want it to look woo woo (meaning airy fairy spiritual stuff!)

```html
<!DOCTYPE html>
<html lang="en">
<head>
<meta charset="utf-8">
<title>9 Paths Home Again</title>
<link rel="stylesheet" href="https://fonts.googleapis.com/css2?family=Great+Vibes&display=swap">
<style>
  :root {
    --water-deep: #2f7fa6;
    --water-mid: #5fa9c6;
    --water-light: #a9d6e2;
    --sand: #c9dcd6;
    --petal-pink: #e46fa3;
    --petal-light: #f6c3d8;
    --petal-core: #c94a86;
    --leaf-green: #3f9a4e;
    --text-white: #ffffff;
    --text-shadow: rgba(20, 60, 90, 0.5);
  }

  html, body {
    margin: 0;
    padding: 0;
    overflow: hidden;
    background: #ffffff;
  }

  .banner {
    position: relative;
    width: 1200px;
    height: 444px;
    overflow: hidden;
  }

  .banner__backdrop {
    position: absolute;
    inset: 0;
    background:
      radial-gradient(ellipse 150px 120px at 420px 250px, var(--petal-core) 0%, rgba(201,74,134,0) 100%),
      radial-gradient(ellipse 300px 230px at 390px 220px, var(--petal-pink) 0%, rgba(228,111,163,0.75) 45%, rgba(228,111,163,0) 100%),
      radial-gradient(ellipse 200px 150px at 480px 330px, var(--petal-light) 0%, rgba(246,195,216,0) 100%),
      radial-gradient(ellipse 200px 120px at 560px 90px, rgba(246,195,216,0.8) 0%, rgba(246,195,216,0) 100%),
      radial-gradient(ellipse 230px 240px at 50px 370px, var(--leaf-green) 0%, rgba(63,154,78,0) 100%),
      radial-gradient(ellipse 170px 200px at 30px 80px, #6fae8a 0%, rgba(111,174,138,0) 100%),
      linear-gradient(115deg, rgba(255,255,255,0) 55%, rgba(255,255,255,0.3) 65%, rgba(255,255,255,0) 72%, rgba(255,255,255,0.25) 80%, rgba(255,255,255,0) 88%),
      radial-gradient(ellipse 520px 170px at 930px 430px, var(--sand) 0%, rgba(201,220,214,0) 100%),
      linear-gradient(180deg, var(--water-mid) 0%, var(--water-deep) 45%, var(--water-mid) 78%, var(--water-light) 100%);
  }

  .banner__title {
    position: absolute;
    left: 0;
    right: 0;
    top: 128px;
    margin: 0;
    text-align: center;
    color: var(--text-white);
    font-family: "Great Vibes", cursive;
    font-weight: 400;
    font-size: 104px;
    line-height: 1.1;
    letter-spacing: 1px;
    text-shadow: 0 2px 12px var(--text-shadow);
  }
</style>
</head>
<body>
  <div class="banner">
    <div class="banner__backdrop" role="img" aria-label="Soft-focus pink lotus flower on the left with green leaves, opening into clear blue underwater light and sandy floor on the right"></div>
    <h1 class="banner__title">9 paths home again</h1>
  </div>
</body>
</html>
```